Corporate Travel Technology Company needs new Business Card design

We need a new business card design to reflect our re-branded company. Our company is called tolvEn (pronounced tolvenn) and we provide Business Intelligence and mobile travel management solutions for the corporate travel industry. Our multinational customers use our solutions to manage large travel budgets and frequent travellers, as well as to save money and reduce risk. We'd like to see designs that use the blue and green palette as well as our corporate logo (attached below). The design should communicate innovation, insight, forward thinking, contemporary, trusted.

Target Market(s)

Large multinational corporates and Travel Agencies.

Industry/Entity Type

Business

Contact Information for Business Card

Rosalind Mercer
Chief Executive
tolvEn
Phone number - +61 (0)2 8134 2907
Email address - rosalind.mercer@tolven-example.com
Mobile number - +61 (0)438 516 702
www.tolven-example.com

Font styles to use
Other font styles liked:
• Please use font as close to corporate logo as possible

Colors
0255a3
0393ce
00a990
33b8a4
33a6d7
3176b5

Requirements
Must have
• Please include the words;
• Mobile Travel Management
• Accelerating Travel Business Insights
• Use corporate logo - although icon can be stylised if needed

```html
<!DOCTYPE html>
<html lang="en">
<head>
<meta charset="utf-8">
<title>tolvEn Business Card</title>
<link rel="stylesheet" href="https://fonts.googleapis.com/css2?family=Montserrat:wght@700&family=Quicksand:wght@400;500;600&display=swap">
<style>
  :root {
    --backdrop: #e9ecee;
    --slate-light: #6f8085;
    --slate-mid: #55666b;
    --slate-dark: #2f3d41;
    --brand-blue: #33a6d7;
    --sky-blue: #2aa9e2;
    --sky-light: #6cc8f0;
    --name-grey: #3a4a50;
    --ink-white: #ffffff;
    --shadow: rgba(20, 30, 35, 0.28);
  }
  * { box-sizing: border-box; margin: 0; padding: 0; }
  html, body {
    width: 1200px; height: 913px; overflow: hidden;
    background: var(--backdrop);
  }
  .canvas {
    position: relative; width: 1200px; height: 913px;
    font-family: "Quicksand", sans-serif;
  }
  .card {
    position: absolute; top: 306px;
    width: 525px; height: 300px;
    border-radius: 4px; overflow: hidden;
    box-shadow: 0 14px 30px var(--shadow);
  }
  .card--front { left: 60px; }
  .card--back { left: 615px; }
  .card__art { position: absolute; inset: 0; display: block; }

  .brand {
    position: absolute; display: flex; align-items: center; gap: 10px;
    font-family: "Quicksand", sans-serif; font-weight: 500;
    line-height: 1;
  }
  .brand__dot { border-radius: 50%; background: currentColor; flex: none; }
  .card--front .brand {
    top: 28px; right: 34px; color: var(--brand-blue); font-size: 54px;
  }
  .card--front .brand__dot { width: 18px; height: 18px; }
  .card--back .brand {
    top: 62px; right: 52px; color: var(--ink-white); font-size: 70px;
  }
  .card--back .brand__dot { width: 24px; height: 24px; }

  .contact {
    position: absolute; left: 30px; bottom: 26px; color: var(--ink-white);
  }
  .contact__name {
    font-family: "Montserrat", sans-serif; font-weight: 700;
    font-size: 19px; letter-spacing: 0.3px; color: var(--name-grey);
    text-transform: uppercase;
  }
  .contact__title {
    font-size: 14px; font-weight: 500; color: var(--name-grey);
    margin: 1px 0 12px;
  }
  .contact__list { list-style: none; }
  .contact__item {
    display: flex; align-items: center; gap: 9px;
    font-size: 13px; font-weight: 500; line-height: 19px;
  }
  .contact__icon { width: 11px; height: 11px; flex: none; }

  .taglines {
    position: absolute; left: 30px; bottom: 28px;
    color: var(--brand-blue); font-size: 17px; font-weight: 600; line-height: 22px;
  }
  .taglines__line { display: flex; align-items: center; gap: 8px; }
  .taglines__mark {
    width: 9px; height: 9px; border-radius: 50%;
    border: 1.5px solid var(--ink-white); flex: none;
  }
</style>
</head>
<body>
<main class="canvas">

  <section class="card card--front" aria-label="Business card front">
    <svg class="card__art" viewBox="0 0 525 300" aria-hidden="true">
      <defs>
        <linearGradient id="front-slate" x1="0" y1="0" x2="1" y2="1">
          <stop offset="0" stop-color="var(--slate-light)"/>
          <stop offset="1" stop-color="var(--slate-mid)"/>
        </linearGradient>
        <linearGradient id="front-sky" x1="0" y1="0" x2="0.6" y2="1">
          <stop offset="0" stop-color="var(--sky-light)"/>
          <stop offset="1" stop-color="var(--sky-blue)"/>
        </linearGradient>
      </defs>
      <rect width="525" height="300" fill="url(#front-slate)"/>
      <path d="M0 112 C170 110 360 150 525 236 L525 300 L0 300 Z" fill="url(#front-sky)"/>
      <path d="M0 96 C170 94 360 134 525 222" fill="none" stroke="var(--ink-white)" stroke-width="4" stroke-linecap="round"/>
    </svg>

    <div class="brand"><span class="brand__dot"></span>tolvEn</div>

    <div class="contact">
      <p class="contact__name">Rosalind Mercer</p>
      <p class="contact__title">Chief Executive</p>
      <ul class="contact__list">
        <li class="contact__item">
          <svg class="contact__icon" viewBox="0 0 12 12"><rect x="3" y="0.5" width="6" height="11" rx="1" fill="none" stroke="currentColor"/><circle cx="6" cy="9.5" r="0.7" fill="currentColor"/></svg>
          +61 (0)438 516 702
        </li>
        <li class="contact__item">
          <svg class="contact__icon" viewBox="0 0 12 12"><path d="M2.5 1 L4.5 1 L5.3 3.6 L4 4.6 C4.7 6 5.9 7.3 7.4 8 L8.4 6.7 L11 7.5 L11 9.5 C11 10.3 10.3 11 9.5 11 C5 11 1 7 1 2.5 C1 1.7 1.7 1 2.5 1 Z" fill="currentColor"/></svg>
          +61 (0)2 8134 2907
        </li>
        <li class="contact__item">
          <svg class="contact__icon" viewBox="0 0 12 12"><circle cx="6" cy="6" r="5" fill="none" stroke="currentColor"/><ellipse cx="6" cy="6" rx="2.2" ry="5" fill="none" stroke="currentColor"/><line x1="1" y1="6" x2="11" y2="6" stroke="currentColor"/></svg>
          www.tolven-example.com
        </li>
        <li class="contact__item">
          <svg class="contact__icon" viewBox="0 0 12 12"><rect x="0.5" y="2.5" width="11" height="7" fill="none" stroke="currentColor"/><path d="M0.5 2.5 L6 6.5 L11.5 2.5" fill="none" stroke="currentColor"/></svg>
          rosalind.mercer@tolven-example.com
        </li>
      </ul>
    </div>
  </section>

  <section class="card card--back" aria-label="Business card back">
    <svg class="card__art" viewBox="0 0 525 300" aria-hidden="true">
      <defs>
        <linearGradient id="back-slate" x1="0" y1="0" x2="0.4" y2="1">
          <stop offset="0" stop-color="var(--slate-light)"/>
          <stop offset="1" stop-color="var(--slate-dark)"/>
        </linearGradient>
      </defs>
      <rect width="525" height="300" fill="url(#back-slate)"/>
    </svg>

    <div class="brand"><span class="brand__dot"></span>tolvEn</div>

    <div class="taglines">
      <p class="taglines__line"><span class="taglines__mark"></span>Mobile Travel Management</p>
      <p class="taglines__line"><span class="taglines__mark"></span>Accelerating Travel Business Insights</p>
    </div>
  </section>

</main>
</body>
</html>
```